Private Investment Firm Needs PowerPoint Presentation Template

Design PowerPoint template, take Pinebrook-submitted rough presentation draft, and drop it into new template. See attached Project Brief file for more detail.
Updates

Some decent designs have been submitted but they seem to lack the understanding of our target markets. I am hopeful that more time and feedback will result in better results.

Target Market(s)

Private company owners and intermediaries.

Font styles to use
Serif

Colors
3176b5

Requirements
Must have
• See attached Project Brief.
Nice to have
Should not have
• No B2C fluff--this is a B2B project.

```html
<!DOCTYPE html>
<html lang="en">
<head>
<meta charset="utf-8">
<title>Pinebrook Capital – Consultants with Capital</title>
<link rel="stylesheet" href="https://fonts.googleapis.com/css2?family=Montserrat:wght@500;600;700&family=Libre+Baskerville&display=swap">
<style>
  :root {
    --brand-blue: #1b6ec2;
    --heading-blue: #1f6fc0;
    --panel-blue: rgba(10, 100, 185, 0.94);
    --photo-dark: #0c2f3e;
    --photo-mid: #2d5f6d;
    --text-gray: #4a4a4a;
    --white: #ffffff;
    --sans: "Montserrat", Arial, sans-serif;
    --serif: "Libre Baskerville", Georgia, serif;
  }
  * { margin: 0; padding: 0; box-sizing: border-box; }
  html, body { width: 1200px; height: 676px; overflow: hidden; background: var(--white); }
  .slide { position: relative; width: 1200px; height: 676px; overflow: hidden; background: var(--white); }

  .side-rail { position: absolute; left: 0; top: 0; width: 44px; height: 100%; background: var(--brand-blue); }
  .edge-rail { position: absolute; right: 0; top: 0; width: 12px; height: 100%; background: var(--brand-blue); }

  .site-url {
    position: absolute; left: 22px; top: 336px;
    transform: translate(-50%, -50%) rotate(-90deg);
    font-family: var(--serif); font-size: 14px; color: var(--white); white-space: nowrap;
  }
  .page-number {
    position: absolute; right: 22px; top: 18px;
    font-family: var(--serif); font-size: 18px; color: #222;
  }

  .section-title {
    position: absolute; left: 86px; top: 84px;
    font-family: var(--sans); font-weight: 600; font-size: 29px; line-height: 33px;
    letter-spacing: 0.5px; color: var(--heading-blue); text-transform: uppercase;
  }

  .value-statement {
    position: absolute; right: 748px; top: 202px; text-align: right;
    font-family: var(--sans); font-weight: 600; font-size: 41px; line-height: 42px;
    color: var(--text-gray);
  }
  .value-statement .lead { color: var(--heading-blue); font-weight: 700; }

  .photo-band {
    position: absolute; left: 483px; top: 101px; width: 705px; height: 470px;
    background: linear-gradient(135deg, var(--photo-dark) 0%, var(--photo-mid) 45%, var(--photo-dark) 100%);
  }

  .services-panel {
    position: absolute; left: 483px; top: 170px; width: 705px; height: 334px;
    background: var(--panel-blue);
  }
  .services-list { list-style: none; position: absolute; left: 61px; top: 12px; width: 620px; }
  .services-list li {
    position: relative; padding-left: 0;
    font-family: var(--sans); font-weight: 500; font-size: 17.5px; line-height: 31.4px;
    color: var(--white);
  }
  .services-list li::before {
    content: ""; position: absolute; left: -24px; top: 11px;
    width: 8px; height: 8px; border: 2.5px solid var(--white);
    transform: rotate(45deg);
  }

  .brand { position: absolute; left: 68px; top: 610px; display: flex; align-items: center; gap: 10px; }
  .brand-mark { width: 34px; height: 34px; border-radius: 50%; background: var(--brand-blue); }
  .brand-text { display: flex; flex-direction: column; }
  .brand-name {
    font-family: var(--serif); font-size: 17px; letter-spacing: 1.5px;
    color: var(--text-gray); text-transform: uppercase; line-height: 20px;
  }
  .brand-tagline {
    font-family: var(--serif); font-size: 7px; letter-spacing: 0.6px;
    color: var(--brand-blue); text-transform: uppercase; margin-top: 3px;
  }
</style>
</head>
<body>
<main class="slide">
  <div class="side-rail"></div>
  <div class="edge-rail"></div>
  <div class="site-url">www.pinebrookcapital.com</div>
  <div class="page-number">13</div>

  <h1 class="section-title">Consultants with<br>Capital</h1>

  <p class="value-statement">
    <span class="lead">We help</span><br>portfolio<br>Companies<br>create<br>greater<br>value.
  </p>

  <div class="photo-band" role="img" aria-label="Close-up photograph of scattered dollar bills in dark teal tones"></div>

  <section class="services-panel">
    <ul class="services-list">
      <li>Facilitate strategy development</li>
      <li>Improve financial reporting and information systems</li>
      <li>Assist with key hires, such as CFOs and COOs, if needed</li>
      <li>Source, evaluate, finance, close, and integrate acquisitions</li>
      <li>Invest additional capital</li>
      <li>Annual Executive Summit focused on professional development and networking</li>
      <li>Most importantly, act as a sounding board to help solve problems, identify new opportunities, and create value</li>
      <li>We personally invest in every transaction</li>
    </ul>
  </section>

  <div class="brand">
    <div class="brand-mark"></div>
    <div class="brand-text">
      <span class="brand-name">Pinebrook Capital</span>
      <span class="brand-tagline">Non-Control Growth Capital</span>
    </div>
  </div>
</main>
</body>
</html>
```